Software Company Banner Ad

We need a banner ad in two sizes. 728x90 and 300x250.
They should have strong similarity to the following ads:
http://www.quellara.com/search/results?brand[0]=zorvik&ad=4812096
http://www.quellara.com/search/results?brand[0]=tralvenco&ad=4826173
Idea will be very similar. We want the same grey color, white text, and a realistic owl that blinks. The owl should have dramatic, bright, yellow eyes. The text will animate "from the top" as in the example. Though the logo animation will be different, all text and non-logo animation should match the animation in the example advertisements. The text will rotate between the following four sentences and images.
Looking for a provider of procurement cloud apps?
[Images - attached below]
The experts really liked our PLW booth.
Get great results with every procurement. [Learn more]
There are three vector files attached below. Feel free to change the colors as necessary to match the color scheme of the ad. We need one 2013 and one 2014 award in the ad.
The awards could appear simultaneously, could swap with each other or could appear in succession. Animation is acceptable.
There is an additional vector file with the company logo. The company logo should go where the Zorvik logo is in horizontal ad. The company logo should go where the Tralvenco logo is in the block ad. The example ad has two logos. We will only need one logo on our ads. The logo should be changed to the color of the text used for the ad (white).
The owls eyes should slowly blink two times (as in the example).
The owl eyes should immediately grab someone's attention and all colors should compliment these eyes.
The [Learn more] button should have animation. The button should match the color of the owl's eyes. There should be a line/gleam/glare of light that travels across the button. The button should be embossed with the subtle animation occurring each time it appears.
Ads should be done with flash. We will need the source files and the names of any fonts used at the end of the project.
Thank you and please do not hesitate to contact with any questions.
Updates
Project Deadline Extended
Reason: We have contacted several photographers to see if the alternative owl images are available on pixHarb, Framelodgery or similar. The duration extension is to accommodate this.
Target Market(s)
Target customers are procurement department employees of large companies.
Industry/Entity Type
It Company

```html
<!DOCTYPE html>
<html lang="en">
<head>
<meta charset="utf-8">
<title>Novarq Procurement Banner</title>
<link href="https://fonts.googleapis.com/css2?family=Oswald:wght@500;600&display=swap" rel="stylesheet">
<style>
  :root {
    --grey-light: #a3a3a3;
    --grey-mid: #7c7c7c;
    --grey-dark: #5a5a5a;
    --white: #ffffff;
    --accent-yellow: #c8e61e;
    --accent-yellow-deep: #8fb40c;
    --button-text: #2f3a08;
    --photo-light: #8a7a6a;
    --photo-mid: #6b5d50;
    --photo-dark: #3f3730;
  }
  html, body {
    margin: 0;
    padding: 0;
    overflow: hidden;
    background: #ffffff;
  }
  .banner {
    position: relative;
    width: 1200px;
    height: 148px;
    overflow: hidden;
    background: linear-gradient(90deg, var(--grey-mid) 0%, #737373 55%, var(--grey-dark) 78%);
    font-family: "Oswald", "Arial Narrow", sans-serif;
  }
  .brand-wedge {
    position: absolute;
    left: 0;
    top: 0;
    width: 240px;
    height: 148px;
  }
  .brand-name {
    position: absolute;
    left: 12px;
    top: 2px;
    margin: 0;
    font-size: 32px;
    font-weight: 600;
    letter-spacing: 2px;
    color: var(--white);
    line-height: 1.2;
  }
  .headline {
    position: absolute;
    left: 238px;
    top: 26px;
    margin: 0;
    color: var(--white);
    font-weight: 600;
    font-size: 31px;
    line-height: 44px;
    text-transform: uppercase;
    letter-spacing: 1.5px;
  }
  .headline-row {
    display: flex;
    align-items: center;
    gap: 14px;
  }
  .learn-more {
    display: inline-flex;
    align-items: center;
    gap: 12px;
    height: 38px;
    padding: 0 10px 0 20px;
    border-radius: 4px;
    background: linear-gradient(180deg, #e2f55a 0%, var(--accent-yellow) 45%, var(--accent-yellow-deep) 100%);
    box-shadow: inset 0 1px 0 rgba(255,255,255,0.6), 0 1px 2px rgba(0,0,0,0.4);
    color: var(--button-text);
    font-size: 22px;
    font-weight: 600;
    letter-spacing: 1px;
    text-decoration: none;
    line-height: 1;
    margin-top: 4px;
  }
  .learn-more svg { display: block; }
  .owl-photo {
    position: absolute;
    right: 0;
    top: 0;
    width: 420px;
    height: 148px;
    background: radial-gradient(ellipse at 65% 55%, var(--photo-light) 0%, var(--photo-mid) 50%, var(--photo-dark) 100%);
    -webkit-mask-image: linear-gradient(90deg, transparent 0%, #000 30%);
    mask-image: linear-gradient(90deg, transparent 0%, #000 30%);
  }
</style>
</head>
<body>
  <div class="banner">
    <svg class="brand-wedge" viewBox="0 0 240 148" aria-hidden="true">
      <defs>
        <linearGradient id="wedgeShade" x1="0" y1="0" x2="1" y2="0">
          <stop offset="0" stop-color="#a8a8a8"/>
          <stop offset="1" stop-color="#8c8c8c"/>
        </linearGradient>
      </defs>
      <polygon points="0,0 215,0 152,148 0,148" fill="url(#wedgeShade)"/>
    </svg>
    <p class="brand-name">NOVARQ</p>

    <h1 class="headline">
      <span>Get great results with every</span><br>
      <span class="headline-row">Procurement.
        <a class="learn-more" href="#">LEARN MORE
          <svg width="24" height="24" viewBox="0 0 24 24" aria-hidden="true">
            <circle cx="12" cy="12" r="11" fill="#4d6608"/>
            <path d="M10 6.5 L15.5 12 L10 17.5" fill="none" stroke="#e2f55a" stroke-width="3" stroke-linecap="round" stroke-linejoin="round"/>
          </svg>
        </a>
      </span>
    </h1>

    <div class="owl-photo" role="img" aria-label="Photograph of a great horned owl with bright yellow eyes"></div>
  </div>
</body>
</html>
```